Electrician Business Card/ company logo/small business

New Business Cards and logo needed that will catch peoples eye and say we went that extra step. Attached is a design possibly to be incorporated, if u have your own great, lets see it!... This will be a small local business. thank you for all you do!
Halvern Electric
Ned Fosky Owner
Journeyman Electrician
phone 1.555.208.3471
email: KQLHalvernElectric@quellmail.net
call for free estimate!
Updates

Accepted and approved for cards

Target Market(s)

support small local business

Industry/Entity Type

Electrical,

Contact Information for Business Card

name, title,company/ logo, phone, email, free estimate

Other font styles liked:
• easy to read

Colors

Designer to choose colors to be used in the design.

Requirements
Must have
• eye catching everything! logo and halvern electric listed on business card/logo, incorp logo in the background of card
Nice to have
• lightening bolts in eyes or around the triangle? vertical, modern, any design that would be unique and stand out
Should not have
• pinks, reds, yellows,brown

```html
<!DOCTYPE html>
<html lang="en">
<head>
<meta charset="utf-8">
<title>Halvern Electric — Business Card</title>
<link href="https://fonts.googleapis.com/css2?family=Michroma&family=Arimo:wght@400&display=swap" rel="stylesheet">
<style>
  :root {
    --backdrop: #2f3032;
    --card-white: #ffffff;
    --brand-blue: #0a64c2;
    --brand-blue-light: #0a8fd8;
    --brand-blue-deep: #0557b0;
    --ink: #1d1d1f;
    --rule: #c9c9c9;
    --ghost: #eeeeee;
  }
  * { box-sizing: border-box; margin: 0; padding: 0; }
  html, body { width: 1200px; height: 866px; overflow: hidden; }
  body {
    background: var(--backdrop);
    font-family: "Arimo", Arial, sans-serif;
    position: relative;
  }
  .card {
    position: absolute;
    top: 278px;
    width: 540px;
    height: 309px;
    overflow: hidden;
  }
  .card--front { left: 40px; background: var(--card-white); }
  .card--back {
    left: 620px;
    background: linear-gradient(135deg, var(--brand-blue-deep) 0%, var(--brand-blue-light) 100%);
  }

  .ghost-name {
    position: absolute;
    left: 10px;
    top: 20px;
    font-family: "Michroma", sans-serif;
    font-size: 96px;
    line-height: 1;
    color: var(--ghost);
    letter-spacing: 2px;
    white-space: nowrap;
  }
  .card--back .ghost-name { color: rgba(255,255,255,0.07); }

  .contact {
    position: absolute;
    left: 36px;
    top: 70px;
    color: var(--ink);
  }
  .contact__name {
    font-family: "Michroma", sans-serif;
    font-size: 20px;
    color: var(--brand-blue);
    letter-spacing: 1px;
  }
  .contact__title { font-size: 14px; margin-top: 4px; }
  .contact__line {
    display: flex;
    align-items: center;
    gap: 8px;
    font-size: 13px;
    margin-top: 8px;
  }
  .contact__line:first-of-type { margin-top: 14px; }
  .contact__line svg { width: 13px; height: 13px; fill: var(--brand-blue); flex: none; }

  .wordmark {
    position: absolute;
    display: flex;
    align-items: center;
    gap: 12px;
    font-family: "Michroma", sans-serif;
    line-height: 1.15;
  }
  .wordmark__dot { border-radius: 50%; flex: none; }
  .card--front .wordmark { right: 30px; top: 112px; color: var(--brand-blue); font-size: 22px; }
  .card--front .wordmark__dot { width: 30px; height: 30px; background: var(--brand-blue); }
  .card--back .wordmark {
    left: 50%; top: 50%; transform: translate(-50%, -50%);
    color: #ffffff; font-size: 28px;
  }
  .card--back .wordmark__dot { width: 40px; height: 40px; background: #ffffff; }

  .divider {
    position: absolute;
    left: 36px; right: 36px; top: 250px;
    height: 1px; background: var(--rule);
  }
  .website {
    position: absolute;
    right: 36px; top: 264px;
    font-size: 14px;
    color: var(--brand-blue);
    letter-spacing: 0.5px;
  }
</style>
</head>
<body>
  <section class="card card--front" aria-label="Business card front">
    <div class="ghost-name" aria-hidden="true">HALVERN</div>
    <div class="contact">
      <h1 class="contact__name">NED FOSKY</h1>
      <p class="contact__title">Journeyman Electrician</p>
      <p class="contact__line">
        <svg viewBox="0 0 24 24" aria-hidden="true"><path d="M6.6 10.8a15 15 0 0 0 6.6 6.6l2.2-2.2a1 1 0 0 1 1-.25 11.4 11.4 0 0 0 3.6.57 1 1 0 0 1 1 1V20a1 1 0 0 1-1 1A17 17 0 0 1 3 4a1 1 0 0 1 1-1h3.5a1 1 0 0 1 1 1c0 1.25.2 2.45.57 3.57a1 1 0 0 1-.25 1z"/></svg>
        1.555.208.3471
      </p>
      <p class="contact__line">
        <svg viewBox="0 0 24 24" aria-hidden="true"><path d="M2 5h20v14H2z M2 5l10 8 10-8" /></svg>
        KQLHalvernElectric@quellmail.net
      </p>
    </div>
    <div class="wordmark">
      <span class="wordmark__dot" aria-hidden="true"></span>
      <span>HALVERN<br>ELECTRIC</span>
    </div>
    <div class="divider"></div>
    <p class="website">www.halvernelectric.com</p>
  </section>

  <section class="card card--back" aria-label="Business card back">
    <div class="ghost-name" aria-hidden="true">HALVERN</div>
    <div class="wordmark">
      <span class="wordmark__dot" aria-hidden="true"></span>
      <span>HALVERN<br>ELECTRIC</span>
    </div>
  </section>
</body>
</html>
```